Managed IT services business card design

We haven't needed a business card since the founding of the business in 2005. All our clients have been coming through word of mouth. And lately more and more existing clients are requesting for our business cards to pass on to their contacts in recommending us.
So we needing a business card design. We use various innovative solutions and methodologies to provide IT services to small businesses in managing their IT systems. Our role is the same as an in-house, full-time IT Manager for our clients, but outsourced. So we take care of all our clients' IT needs, just as an IT Manager would be expected to perform.
We have a holding website, which we're happy to leave for now. If we can use the same logo would be great - www.lumadesk.com.au
Preferred colours are shades of are white, grey and black.
We pride our business with the following traits: proactive, good service, prompt response, trustworthy.
Target Market(s)
Small businesses of any industry
Industry/Entity Type
Business

```html
<!DOCTYPE html>
<html lang="en">
<head>
<meta charset="utf-8">
<title>Lumadesk Business Card</title>
<link rel="stylesheet" href="https://fonts.googleapis.com/css2?family=Arimo:wght@400;700&family=Exo+2:wght@400&display=swap">
<style>
  :root {
    --page: #e9e7e3;
    --card-dark: #3f3f40;
    --card-dark-deep: #2f2f30;
    --card-white: #ffffff;
    --accent-blue: #2a6fd6;
    --accent-blue-light: #59a9f0;
    --ink: #1e1e1e;
    --line: #f2f2f2;
    --muted: #d9d9d9;
  }
  * { box-sizing: border-box; margin: 0; padding: 0; }
  html, body {
    width: 1200px; height: 1050px; overflow: hidden;
    background: var(--page);
  }
  .canvas { position: relative; width: 1200px; height: 1050px; }
  .card {
    position: absolute; top: 140px; width: 440px; height: 770px;
    overflow: hidden; border-radius: 3px;
    box-shadow: 0 14px 32px rgba(0,0,0,0.22);
  }
  .card--front { left: 120px; background: linear-gradient(160deg, #4b4b4c 0%, var(--card-dark) 55%, var(--card-dark-deep) 100%); }
  .card--back { left: 640px; background: var(--card-white); }

  .header-band {
    position: absolute; left: 0; top: 22px; width: 100%; height: 180px;
    background: var(--card-white);
    border-top: 5px solid var(--accent-blue);
    border-bottom: 5px solid var(--accent-blue);
    box-shadow: inset 0 2px 0 var(--accent-blue-light), inset 0 -2px 0 var(--accent-blue-light);
  }
  .brand-name {
    position: absolute; left: 0; top: 52px; width: 100%; text-align: center;
    font-family: "Arimo", sans-serif; font-weight: 400;
    font-size: 40px; letter-spacing: 0; color: var(--ink);
  }

  .connectors { position: absolute; left: 0; top: 0; width: 440px; height: 770px; }

  .name-box {
    position: absolute; left: 186px; top: 188px; width: 236px; height: 84px;
    background: var(--card-white); padding: 14px 0 0 18px;
  }
  .person-name {
    font-family: "Arimo", sans-serif; font-weight: 700;
    font-size: 24px; color: var(--ink); letter-spacing: 0.5px;
  }
  .person-title {
    font-family: "Exo 2", sans-serif; font-size: 15px; color: var(--ink); margin-top: 4px;
  }

  .contact-box {
    position: absolute; left: 130px; width: 282px; height: 82px;
    border: 2px solid var(--line); color: var(--line);
    text-align: center; padding-top: 14px;
  }
  .contact-box--phone { top: 320px; }
  .contact-box--email { top: 430px; }
  .contact-box--web { top: 540px; }
  .contact-label {
    font-family: "Arimo", sans-serif; font-weight: 700; font-size: 19px; letter-spacing: 0.5px;
  }
  .contact-value {
    font-family: "Exo 2", sans-serif; font-size: 16px; margin-top: 6px; color: var(--muted);
  }

  .address-rule {
    position: absolute; left: 20px; top: 668px; width: 400px; height: 3px;
    background: linear-gradient(90deg, rgba(255,255,255,0) 0%, #cfcfcf 30%, #ffffff 55%, #bdbdbd 80%, rgba(255,255,255,0) 100%);
  }
  .address {
    position: absolute; left: 0; top: 694px; width: 100%; text-align: center;
    font-family: "Exo 2", sans-serif; font-weight: 400; font-size: 18px;
    letter-spacing: 1px; color: var(--line);
  }

  .back-lower {
    position: absolute; left: 0; top: 440px; width: 100%; height: 330px;
    background: linear-gradient(160deg, #4b4b4c 0%, var(--card-dark) 55%, var(--card-dark-deep) 100%);
  }
  .back-address {
    position: absolute; left: 0; top: 120px; width: 100%; text-align: center;
    font-family: "Exo 2", sans-serif; font-size: 22px; line-height: 1.6;
    letter-spacing: 1px; color: var(--line);
  }
</style>
</head>
<body>
<div class="canvas">

  <section class="card card--front" aria-label="Business card front">
    <div class="header-band">
      <p class="brand-name">lumadesk</p>
    </div>

    <svg class="connectors" viewBox="0 0 440 770" aria-hidden="true">
      <g fill="none" stroke="#f2f2f2" stroke-width="2">
        <polyline points="186,236 62,236 62,580"/>
        <line x1="62" y1="338" x2="130" y2="338"/>
        <line x1="62" y1="448" x2="130" y2="448"/>
        <line x1="62" y1="558" x2="130" y2="558"/>
      </g>
    </svg>

    <div class="name-box">
      <p class="person-name">DANIEL REYES</p>
      <p class="person-title">Managing Director</p>
    </div>

    <div class="contact-box contact-box--phone">
      <p class="contact-label">PHONE</p>
      <p class="contact-value">012 555 0148</p>
    </div>
    <div class="contact-box contact-box--email">
      <p class="contact-label">EMAIL</p>
      <p class="contact-value">hello@lumadesk.com.au</p>
    </div>
    <div class="contact-box contact-box--web">
      <p class="contact-label">WEBSITE</p>
      <p class="contact-value">www.lumadesk.com.au</p>
    </div>

    <div class="address-rule"></div>
    <p class="address">027.9th floor,Harbour Crest Road NSW</p>
  </section>

  <section class="card card--back" aria-label="Business card back">
    <div class="back-lower">
      <p class="back-address">027.9th floor,Harbour<br>Crest Road NSW</p>
    </div>
  </section>

</div>
</body>
</html>
```